Kelvor Engineers: Why you should hire us keepsake

New design. Open to plastic cards. We are an engineering firm that designs cell phone towers and commercial buildings. Please check out our website www.kelvorstruct.com for more details. We want people to remember our card and for it to be useful if possible. We want the same look and feel on these cards to be translated to other marketing material we may need such as brochures.

Target Market(s)

Architects, Developers and Telecommunication Carriers

Industry/Entity Type

Engineering

Contact Information for Business Card

Card with our company colors, logo, and innovative design with elements related to our industry.

Font styles to use
Sans Serif

Colors
9bcb3c
abd036
0255a3

Requirements
Must have
• Sleek and hip design
Nice to have
• Bright lime green and navy coloring that pops with an innovative design.
Should not have
• A basic and boring design

```html
<!DOCTYPE html>
<html lang="en">
<head>
<meta charset="utf-8">
<title>Kelvor Engineers – Business Card</title>
<link href="https://fonts.googleapis.com/css2?family=Montserrat:wght@400;500;800&display=swap" rel="stylesheet">
<style>
  :root {
    --page-bg: #e9edf1;
    --card-top: #f7f8f9;
    --navy: #16284a;
    --navy-text: #1a2a4a;
    --lime: #22e01a;
    --lime-soft: #3bd43a;
    --light-text: #c9d2e0;
    --divider: rgba(255,255,255,0.14);
  }
  * { box-sizing: border-box; margin: 0; padding: 0; }
  html, body {
    width: 1200px; height: 900px; overflow: hidden;
    background: var(--page-bg);
    font-family: "Montserrat", Arial, sans-serif;
  }
  .business-card {
    position: absolute; left: 226px; top: 237px;
    width: 748px; height: 426px;
    border-radius: 14px; overflow: hidden;
    box-shadow: 0 12px 30px rgba(20,40,70,0.18);
  }
  .card-head {
    position: absolute; left: 0; top: 0; width: 100%; height: 192px;
    background: var(--card-top);
  }
  .brand-name {
    position: absolute; left: 42px; top: 62px;
    font-weight: 800; font-size: 46px; letter-spacing: -0.5px;
    color: var(--lime); line-height: 1;
  }
  .tagline {
    position: absolute; right: 41px; top: 123px;
    font-size: 17px; font-weight: 500; color: var(--navy-text);
  }
  .accent-rule {
    position: absolute; left: 0; top: 192px; width: 100%; height: 5px;
    background: var(--lime);
  }
  .card-body {
    position: absolute; left: 0; top: 197px; width: 100%; height: 229px;
    background: var(--navy);
  }
  .person-name {
    position: absolute; left: 42px; top: 54px;
    font-size: 21px; font-weight: 400; color: var(--lime-soft);
  }
  .body-divider {
    position: absolute; left: 42px; right: 41px; top: 92px;
    height: 1px; background: var(--divider);
  }
  .contact-list {
    position: absolute; left: 42px; top: 106px; list-style: none;
  }
  .contact-list li {
    display: flex; align-items: center; gap: 7px;
    font-size: 16.5px; color: var(--light-text); height: 23.5px;
  }
  .contact-list svg { width: 12px; height: 12px; fill: var(--lime-soft); }
  .office {
    position: absolute; right: 41px; top: 106px; text-align: right;
    font-size: 16.5px; color: var(--light-text); line-height: 23px;
  }
  .office .website { margin-top: 7px; }
  .office .website span { color: var(--lime-soft); }
</style>
</head>
<body>
  <div class="business-card">
    <div class="card-head">
      <div class="brand-name">Kelvor Engineers</div>
      <div class="tagline">Multi-discipline engineering</div>
    </div>
    <div class="accent-rule"></div>
    <div class="card-body">
      <div class="person-name">Dana Whitfield Orr</div>
      <div class="body-divider"></div>
      <ul class="contact-list">
        <li>
          <svg viewBox="0 0 12 12" aria-hidden="true"><path d="M2.5 1 L4.5 1 L5 3.5 L3.8 4.4 C4.5 6 6 7.5 7.6 8.2 L8.5 7 L11 7.5 L11 9.5 C11 10.3 10.3 11 9.5 11 C5 11 1 7 1 2.5 C1 1.7 1.7 1 2.5 1 Z"/></svg>
          555.014.2210
        </li>
        <li>
          <svg viewBox="0 0 12 12" aria-hidden="true"><path d="M3.5 0.5 H8.5 A1 1 0 0 1 9.5 1.5 V10.5 A1 1 0 0 1 8.5 11.5 H3.5 A1 1 0 0 1 2.5 10.5 V1.5 A1 1 0 0 1 3.5 0.5 Z M3.7 2 V9 H8.3 V2 Z M6 9.6 A0.6 0.6 0 1 0 6 10.8 A0.6 0.6 0 1 0 6 9.6 Z"/></svg>
          555.019.7734
        </li>
        <li>
          <svg viewBox="0 0 12 12" aria-hidden="true"><path d="M1 2.5 H11 V9.5 H1 Z M1.6 3 L6 6.6 L10.4 3 Z" fill-rule="evenodd"/></svg>
          dorr@kelvorstruct.com
        </li>
      </ul>
      <div class="office">
        <div>2400 Larkspur Ridge Pkwy.</div>
        <div>Suite 310 Aldermoor, GA 30000</div>
        <div class="website">www.<span>kelvorstruct</span>.com</div>
      </div>
    </div>
  </div>
</body>
</html>
```